Business Card Design

Electronic Security Installation Specialists

Check out our website at www.tallbrookllc.com to see what we do.

Industry/Entity Type

Business

Contact Information for Business Card

Tall Brook
Marjorie Hadley
281 Orchard Rise
Mapleton, WV 25871

Colors
3176b5
0455a3
ffffff

```html
<!DOCTYPE html>
<html lang="en">
<head>
<meta charset="utf-8">
<title>Tall Brook – Business Card</title>
<link rel="stylesheet" href="https://fonts.googleapis.com/css2?family=Open+Sans:wght@400;600;700&display=swap">
<style>
  :root {
    --brand-blue: #3176b5;
    --brand-navy: #0455a3;
    --paper: #ffffff;
    --backdrop: #e9ebee;
    --ink-soft: #5b7fa6;
  }
  * { box-sizing: border-box; margin: 0; padding: 0; }
  html, body { width: 1200px; height: 913px; overflow: hidden; }
  body {
    position: relative;
    background: var(--backdrop);
    font-family: "Open Sans", sans-serif;
  }
  .card {
    position: absolute;
    width: 560px;
    height: 320px;
    background: var(--paper);
    box-shadow: 0 6px 18px rgba(0,0,0,0.18);
    overflow: hidden;
  }
  .card-front { left: 60px; top: 70px; }
  .card-back { left: 580px; top: 520px; }

  .brand {
    position: absolute;
    display: flex;
    align-items: center;
    gap: 14px;
    white-space: nowrap;
  }
  .brand-dot {
    width: 34px; height: 34px;
    border-radius: 50%;
    background: var(--brand-navy);
    flex: none;
  }
  .brand-name {
    font-weight: 700;
    color: var(--brand-navy);
    letter-spacing: 0.5px;
  }
  .card-front .brand { left: 50%; top: 50%; transform: translate(-50%, -50%); }
  .card-front .brand-name { font-size: 40px; }
  .card-back .brand { left: 40px; top: 98px; }
  .card-back .brand-name { font-size: 30px; }
  .card-back .brand-dot { width: 26px; height: 26px; }

  .person {
    position: absolute;
    right: 36px; top: 28px;
    text-align: right;
    white-space: nowrap;
  }
  .person-name { font-size: 20px; font-weight: 700; color: var(--brand-blue); }
  .person-role { font-size: 12px; color: var(--ink-soft); }

  .band { position: absolute; inset: 0; }

  .contact {
    position: absolute;
    left: 28px; bottom: 16px;
    list-style: none;
    color: var(--paper);
    font-size: 12.5px;
    line-height: 20px;
    white-space: nowrap;
  }
  .contact li { display: flex; align-items: center; gap: 10px; }
  .contact .icon { width: 12px; height: 12px; flex: none; }

  .website {
    position: absolute;
    right: 24px; top: 214px;
    color: var(--paper);
    font-size: 12.5px;
    white-space: nowrap;
  }
</style>
</head>
<body>

  <section class="card card-front">
    <div class="brand">
      <span class="brand-dot"></span>
      <span class="brand-name">Tall Brook</span>
    </div>
  </section>

  <section class="card card-back">
    <div class="person">
      <div class="person-name">Marjorie Hadley</div>
      <div class="person-role">Managing Director</div>
    </div>

    <div class="brand">
      <span class="brand-dot"></span>
      <span class="brand-name">Tall Brook</span>
    </div>

    <svg class="band" viewBox="0 0 560 320" aria-hidden="true">
      <rect x="0" y="200" width="560" height="120" fill="var(--brand-blue)"/>
      <polygon points="0,250 290,170 310,200 310,320 0,320" fill="var(--brand-navy)"/>
    </svg>

    <ul class="contact">
      <li><svg class="icon" viewBox="0 0 12 12" aria-hidden="true"><path fill="var(--paper)" d="M2 1h3l1 3-1.5 1a6 6 0 0 0 2.5 2.5L8 6l3 1v3a1 1 0 0 1-1 1A9 9 0 0 1 1 2a1 1 0 0 1 1-1z"/></svg>301-555-0186</li>
      <li><svg class="icon" viewBox="0 0 12 12" aria-hidden="true"><rect x="0.5" y="2.5" width="11" height="7" fill="var(--paper)"/><path d="M0.5 2.5l5.5 4 5.5-4" fill="none" stroke="var(--brand-navy)" stroke-width="1"/></svg>m.hadley@tallbrookllc.com</li>
      <li><svg class="icon" viewBox="0 0 12 12" aria-hidden="true"><path fill="var(--paper)" d="M6 0a4 4 0 0 1 4 4c0 3-4 8-4 8S2 7 2 4a4 4 0 0 1 4-4zm0 2.5a1.5 1.5 0 1 0 0 3 1.5 1.5 0 0 0 0-3z"/></svg>281 Orchard Rise Mapleton, WV 25871</li>
    </ul>

    <div class="website">www.tallbrookllc.com</div>
  </section>

</body>
</html>
```